Lotstallmart.com Webpage Design

Design Brief for lotstallmart.com (Copy of Brief also in attached Word file)

Name of Website- lotstallmart.com (existing logo and look & feel of website to be changed)

Logo - Finalised. The logo files are attached with the brief as “logo.jpeg”. The “Blue- Grey” version of the logo is for use on lighter backgrounds and the “Orange-White” version of the logo is for use on darker backgrounds. (A full Black version of the logo is also attached). Both versions may be used in different parts of the website. All attached files are in .png format.
Status - The website in functional and is undergoing user trials. However, we want to improve the look & feel of the website so at it seems
a. cotemporary,
b. Easy to Navigate
c. professional and
d. Vibrant.

Please visit ‘lotstallmart.com’ to check out the website and its functionalities – please use it only as a reference for the features & functions to be provided, however the designer should use a ‘Free Hand’ in designing the composition of various parts of the webpage without getting too influenced by the existing design

Objective of the Website ‘lotstallmart.com –
a. It is a portal focussed on listing of ‘Retail’ specific real-estate properties by developers, owners and realty brokers. The properties shall listed under the following four categories-
i. Retail Malls
ii. Shopping Complexes
iii. High-street shops
iv. Retail Warehouses
*refer lotstallmart.com for better clarity

b. The abovementioned properties shall be listed either for ‘Sale’ or ‘rent\lease’ or both

c. Users shall visit the site in case they wish to acquire a retail \ shop space either on ‘sale’ or ‘rent’. These Users would be able to specify the ‘Search Criteria’ through the tool-bars provided on the website – the ‘Search Criteria’ shall comprise of ‘Type of space category’, ‘City’, ‘Locality’, transaction type ie ‘Rent \ Sale’ and ‘Area Range’

d. The main revenue model for the website shall be listing fee ( or advertising charges ) payable by those listing their properties on the website.

Three Main Pages of Website (lotstallmart.com) that need to be designed -
a. Main Home Page (visit the web link - http://lotstallmart.com/ ) - The main home page has the “Search Toolbar” for specifying of Search Criteria by the User. It shall also have the following features & functions-
i. Main Advertising Banner
ii. Featured Projects
iii. New Launches
iv. Toolbar with buttons – ‘Advertise with Us’, ‘Listings Alert’, ‘Mart Wizards’, ‘Advertiser Login’

b. Property Listings Page (visit the web link - http://lotstallmart.com/gurgaon-in-india ) - The List of property options that match the Criteria specified by the ‘User’ get displayed on this page.

c. Property Detail Page - When the ‘User’ clicks on the “More….” Button on the ‘Property Listings Page’ (given in point b. above) the web page with the details of the property opens. (For Example – visit the web link - http://lotstallmart.com/vorne-Shopping-Complex-vorne-quadrion-gurgaon-636 )

Note:- Please refer to attached ‘Shopping’ related images the designer may use them on the website to provide a look & feel of retail if required – either separately or rotate in a single window

Target Market(s)

Retailers & Investors looking for retail space, Real Estate Brokers, Developers

Industry/Entity Type

Advertising

Number of Pages Required

3 page

Requirements
Must have
• Refer to existing site lotstallmart.com -- all the existing functionalities are a must have.
Nice to have
• The Designer may use the retail related images on the website if required for making it more vibrant. Refer attached images Shopping(1-6).jpg

```html
<!DOCTYPE html>
<html lang="en">
<head>
<meta charset="utf-8">
<title>Lotstallmart.com – Retail Space Portal</title>
<link href="https://fonts.googleapis.com/css2?family=Open+Sans:wght@400;600;700&display=swap" rel="stylesheet">
<style>
:root{
  --bar:#5a5a5c; --bar-text:#e6e6e6; --blue:#1e96d8; --blue-dark:#1478b4; --blue-deep:#1a6aa6;
  --orange:#f7890f; --orange-btn:#f39a1e; --green:#6cb33e; --page:#ececec; --white:#fff;
  --text:#333; --muted:#8a8a8a; --title:#e87c12; --footer:#5b5b5d; --footer-low:#4a4a4c; --line:#d8d8d8;
}
*{box-sizing:border-box;margin:0;padding:0}
html,body{width:681px;height:1200px;overflow:hidden}
body{position:relative;font-family:'Open Sans',Arial,sans-serif;background:var(--page);color:var(--text);font-size:7px}
.abs{position:absolute}
.city-bar{left:0;top:0;width:681px;height:21px;background:var(--bar);display:flex;justify-content:center}
.city-bar span{color:var(--bar-text);font-size:6.6px;line-height:21px;width:52px;text-align:center;border-right:1px solid #666}
.city-bar span:first-child{border-left:1px solid #666}
.header{left:0;top:21px;width:681px;height:48px;background:var(--white)}
.brand{left:56px;top:30px;display:flex;align-items:center;gap:4px}
.brand .dot{width:13px;height:13px;border-radius:50%;background:var(--blue)}
.brand b{font-size:14px;font-weight:700;color:var(--blue-deep)}
.brand small{display:block;font-size:4.2px;color:var(--muted);letter-spacing:.3px;text-transform:uppercase}
.nav-item{top:21px;height:48px;padding:15px 0 0 14px;border-left:1px solid #e3e3e3;width:102px}
.nav-item strong{display:block;font-size:5.8px;font-weight:400;color:#444}
.nav-item em{font-style:normal;font-size:5.8px;color:var(--muted)}
.login{left:526px;width:98px;height:24px;color:#fff;font-size:6.6px;font-weight:700;text-align:center;line-height:24px}
.hero{left:0;top:69px;width:681px;height:266px;background:
  radial-gradient(ellipse 120px 150px at 290px 130px,rgba(240,228,205,.75),transparent 70%),
  radial-gradient(ellipse 90px 130px at 420px 150px,rgba(214,90,140,.55),transparent 70%),
  radial-gradient(ellipse 140px 90px at 560px 80px,rgba(255,214,150,.7),transparent 70%),
  radial-gradient(ellipse 70px 60px at 440px 230px,rgba(226,110,200,.6),transparent 70%),
  radial-gradient(ellipse 80px 100px at 340px 220px,rgba(80,110,190,.55),transparent 70%),
  linear-gradient(180deg,#7a6550 0%,#b7a07a 30%,#a08a6a 60%,#5c5248 85%,#3e3a36 100%)}
.search-panel{left:0;top:90px;width:200px;height:210px;background:var(--blue);padding:16px 0 0 17px;color:#fff}
.search-panel h4{font-size:5.8px;font-weight:400;margin-bottom:8px}
.format-box{width:150px;height:40px;border:1px solid rgba(255,255,255,.35);display:grid;grid-template-columns:1fr 1fr;padding:7px 0 0 10px;row-gap:7px;font-size:5px}
.format-box span::before{content:"";display:inline-block;width:5px;height:5px;border:1px solid rgba(255,255,255,.5);margin-right:4px;vertical-align:-1px}
.field{width:150px;height:18px;border:1px solid rgba(255,255,255,.35);margin-top:6px;font-size:5.2px;line-height:16px;padding-left:7px;position:relative}
.field::after{content:"▾";position:absolute;right:6px;top:0}
.search-btn{margin:10px 0 0 82px;width:69px;height:21px;background:var(--orange-btn);font-size:6px;line-height:21px;text-align:center}
.side-label{left:176px;top:118px;width:20px;height:90px;writing-mode:vertical-rl;transform:rotate(180deg);font-size:6.4px;font-weight:700;color:#fff;text-align:center}
.cat-tab{left:494px;width:108px;height:45px;padding:12px 0 0 14px;color:#fff;border-bottom:1px solid rgba(255,255,255,.2)}
.cat-tab b{display:block;font-size:6.6px;color:#9fdcff;font-weight:600}
.cat-tab span{font-size:4.6px}
.wizards{left:494px;top:472px;width:130px;height:214px;background:var(--orange);padding:16px 14px;color:#fff}
.wizards h3{font-size:7px;font-weight:700;margin-bottom:7px}
.wizards p{font-size:5.6px;line-height:11.5px}
.input{height:18px;background:#fff;border:1px solid #ddd;font-size:5.2px;color:#999;padding:5px 7px;margin-top:7px}
.btn-blue{background:var(--blue-deep);color:#fff;font-size:5.6px;font-weight:600;text-align:center;height:18px;line-height:18px}
.alert-box{left:494px;top:688px;width:130px;height:166px;background:#f4f4f4;padding:10px 14px}
.alert-box h3,.about-box h3{font-size:6.8px;color:var(--blue-deep);font-weight:700;margin-bottom:5px}
.alert-box p,.about-box p{font-size:5.6px;line-height:11.5px;color:var(--muted)}
.about-box{left:494px;top:860px;width:130px;height:172px;background:#f4f4f4;padding:14px 14px}
.section-title{left:58px;font-size:8.6px;font-weight:700;color:#333}
.section-title span{font-size:6px;font-weight:400}
.arrows{left:463px;font-size:7px;color:#999}
.panel{left:58px;width:420px;height:308px;background:#fff;display:grid;grid-template-columns:repeat(4,93px);column-gap:10.3px;row-gap:11px;padding:10px 9px}
.card .photo{height:82px;position:relative}
.card .photo span{position:absolute;left:0;bottom:0;width:100%;height:17px;background:rgba(0,0,0,.55);color:#fff;font-size:6.4px;line-height:17px;padding-left:9px}
.card h5{font-size:6.8px;color:var(--title);font-weight:400;margin:9px 0 2px 3px}
.card p{font-size:5.6px;color:var(--muted);margin-left:3px}
.card .view{margin-top:7px;height:22px;border:1px solid var(--line);color:#999;font-size:6.2px;text-align:center;line-height:20px}
.card .view.on{background:var(--orange-btn);border-color:var(--orange-btn);color:#fff}
.footer{left:0;top:1048px;width:681px;height:125px;background:var(--footer);color:#ddd}
.footer h4,.fcol h4{font-size:7px;font-weight:700;color:#fff;margin-bottom:8px}
.fcol{top:1066px;font-size:5.6px;line-height:11.3px;color:#ddd}
.links{display:grid;grid-template-columns:60px 60px;font-size:5.4px;line-height:13.7px}
.links span::before{content:"› "}
.social{display:grid;grid-template-columns:72px 72px;row-gap:8px;font-size:5.4px}
.social span::before{content:"";display:inline-block;width:11px;height:11px;border:1px solid #999;margin-right:4px;vertical-align:-3px}
.copyright{left:0;top:1173px;width:681px;height:27px;background:var(--footer-low);color:#ccc;font-size:5.6px;text-align:center;line-height:27px}
</style>
</head>
<body>
<nav class="abs city-bar">
  <span>Bangalore</span><span>Chennai</span><span>Greater Noida</span><span>Gurgaon</span><span>Hyderabad</span><span>Jaipur</span><span>Khanna</span><span>Kolkatta</span><span>Mumbai</span><span>Noida</span><span>Pune</span><span>Surat</span>
</nav>
<header class="abs header"></header>
<div class="abs brand"><i class="dot"></i><div><b>lotstallmart</b><small>India's leading portal for retail space</small></div></div>
<div class="abs nav-item" style="left:219px"><strong>ADVERTISE WITH US</strong><em>Standard listing - FREE »</em></div>
<div class="abs nav-item" style="left:321px"><strong>MART WIZARDS</strong><em>Shop Search Services »</em></div>
<div class="abs nav-item" style="left:423px"><strong>LISTING ALERT</strong><em>Shop Search Services »</em></div>
<div class="abs login" style="top:21px;background:var(--green)">ADVERTISER LOGIN »</div>
<div class="abs login" style="top:45px;background:var(--orange)">NEW REGISTER LOGIN »</div>

<div class="abs hero" role="img" aria-label="Family walking through a bright shopping mall carrying colourful shopping bags"></div>
<form class="abs search-panel">
  <h4>Select Retail Format: Meaning of Retail Format</h4>
  <div class="format-box"><span>Retail Malls</span><span>Shopping Complex</span><span>High Street Shops</span><span>Retail Warehouses</span></div>
  <div class="field">Sale Or Rent Or Both:</div>
  <div class="field">Select City:</div>
  <div class="field">Select Locality/Micro-Market:</div>
  <div class="field">Enter Keywords:</div>
  <div class="search-btn">⌕ Seach Now</div>
</form>
<div class="abs side-label">SELECT YOUR FAVORITE</div>
<svg class="abs" style="left:202px;top:97px" width="10" height="10" viewBox="0 0 10 10"><circle cx="4" cy="4" r="3" fill="none" stroke="#fff" stroke-width="1.4"/><line x1="6.2" y1="6.2" x2="9" y2="9" stroke="#fff" stroke-width="1.6"/></svg>

<div class="abs cat-tab" style="top:289px;background:var(--blue-dark)"><b>RETAIL MALLS</b><span>CENTRALLY AIR-CONDITIONED ⊙</span></div>
<div class="abs cat-tab" style="top:335px;background:var(--blue)"><b>SHOPPING COMPLEX</b><span>NON AIR-CONDITIONED BUILDING ⊙</span></div>
<div class="abs cat-tab" style="top:381px;background:var(--blue)"><b>HIGH STREET SHOPS</b><span>ROAD FACING RETAIL ⊙</span></div>
<div class="abs cat-tab" style="top:427px;background:var(--blue)"><b>RETAIL WAREHOUSES</b><span>BACK-END RATAIL STORAGE ⊙</span></div>

<aside class="abs wizards">
  <h3>MART WIZARDS</h3>
  <p>Post your Retail Space requirement with us and our experts shall get back with suitable options and even help you in your transaction. This is a Free Service!</p>
  <div class="input">Enter your email address :</div>
  <div class="input">Mobile :</div>
  <div class="input" style="height:33px">Discription of requirement :</div>
  <div class="btn-blue" style="width:52px;margin:10px 0 0 53px">SEND</div>
</aside>
<aside class="abs alert-box">
  <h3>LISTING ALERT</h3>
  <p>Suscribe for Fortnightly Email update on New Listings @ Lotstallmart</p>
  <div class="input">Enter your email address :</div>
  <div class="input">Select option : ▾</div>
  <div class="input">select cities of interest ▾</div>
  <div class="btn-blue" style="width:56px;margin:7px 0 0 48px">SUBSCRIBE</div>
</aside>
<aside class="abs about-box">
  <h3>WWW.LOTSTALLMART.COM</h3>
  <p>Lotstallmart.com - About Us Lotstallmart.com is a Specialised Web based platform for Retail Space, featuring properties across India under various formats such as Retail Malls.</p>
  <p style="margin-top:8px">Retail Space, featuring properties across India under various...</p>
  <p style="margin-top:6px;color:var(--blue-deep)">[ Read More + ]</p>
</aside>

<h2 class="abs section-title" style="top:353px">FEATURED RETAIL PROJECTS <span>ACROSS INDIA</span></h2>
<div class="abs arrows" style="top:354px">‹ ›</div>
<section class="abs panel" style="top:376px">
  <div class="card"><div class="photo" role="img" aria-label="Glass-fronted shopping complex under blue sky" style="background:radial-gradient(ellipse 40px 30px at 45px 45px,rgba(200,230,255,.6),transparent),linear-gradient(#5f9fe0,#9cc4e8 35%,#6f8aa6 55%,#4a5868 80%,#2e3640)"><span>Surat</span></div><h5>Corvel Arcade</h5><p>Shopping Complex</p><div class="view on">View the listing</div></div>
  <div class="card"><div class="photo" role="img" aria-label="Mall lit up at dusk" style="background:radial-gradient(ellipse 50px 22px at 46px 48px,rgba(255,190,90,.85),transparent),linear-gradient(#22345e,#3f4f7c 35%,#7a5a3e 60%,#2a2422)"><span>Fairdabad</span></div><h5>Corvel Arcade</h5><p>Shopping Complex</p><div class="view">View the listing</div></div>
  <div class="card"><div class="photo" role="img" aria-label="Modern retail building with glass canopy" style="background:radial-gradient(ellipse 45px 25px at 40px 40px,rgba(240,245,250,.8),transparent),linear-gradient(#8fb8dc,#c5d6e2 35%,#8c969a 60%,#4f5558)"><span>Gurgaon</span></div><h5>Corvel Arcade</h5><p>Shopping Complex</p><div class="view">View the listing</div></div>
  <div class="card"><div class="photo" role="img" aria-label="High-rise retail towers" style="background:radial-gradient(ellipse 20px 45px at 50px 40px,rgba(120,130,140,.7),transparent),linear-gradient(#eef2f5,#c6cdd2 45%,#7f8b8f 70%,#4d575a)"><span>Surat</span></div><h5>Corvel Arcade</h5><p>Shopping Complex</p><div class="view">View the listing</div></div>
  <div class="card"><div class="photo" role="img" aria-label="Colourful mall with bright signage" style="background:radial-gradient(ellipse 30px 35px at 55px 40px,rgba(250,210,40,.9),transparent),radial-gradient(ellipse 22px 30px at 20px 45px,rgba(220,60,50,.75),transparent),linear-gradient(#2a3a6a,#6b4a2a 50%,#2a1f18)"><span>Surat</span></div><h5>Corvel Arcade</h5><p>Shopping Complex</p><div class="view">View the listing</div></div>
  <div class="card"><div class="photo" role="img" aria-label="Cinema mall entrance at night" style="background:radial-gradient(ellipse 35px 30px at 46px 45px,rgba(255,150,40,.8),transparent),radial-gradient(ellipse 15px 20px at 50px 20px,rgba(60,120,220,.8),transparent),linear-gradient(#11161e,#3a2a1e 60%,#1a140f)"><span>Fairdabad</span></div><h5>Corvel Arcade</h5><p>Shopping Complex</p><div class="view">View the listing</div></div>
  <div class="card"><div class="photo" role="img" aria-label="Busy shopping street building" style="background:radial-gradient(ellipse 40px 25px at 45px 40px,rgba(230,140,60,.75),transparent),linear-gradient(#b6c6d2,#9c8a72 45%,#6a4a38 70%,#3a2e28)"><span>Gurgaon</span></div><h5>Corvel Arcade</h5><p>Shopping Complex</p><div class="view">View the listing</div></div>
  <div class="card"><div class="photo" role="img" aria-label="Glass retail centre" style="background:radial-gradient(ellipse 40px 25px at 50px 45px,rgba(120,200,230,.7),transparent),linear-gradient(#e6eef3,#a9c0cf 40%,#6e8796 65%,#47565e)"><span>Surat</span></div><h5>Corvel Arcade</h5><p>Shopping Complex</p><div class="view">View the listing</div></div>
</section>

<h2 class="abs section-title" style="top:698px">FEATURED NEW LAUNCHES <span>ACROSS INDIA</span></h2>
<div class="abs arrows" style="top:699px">‹ ›</div>
<section class="abs panel" style="top:722px">
  <div class="card"><div class="photo" role="img" aria-label="Low-rise shopping centre" style="background:radial-gradient(ellipse 45px 25px at 46px 48px,rgba(230,190,150,.9),transparent),linear-gradient(#3f7fd0,#8ab2e0 35%,#b08e70 60%,#5a4a3c)"><span>Surat</span></div><h5>Corvel Arcade</h5><p>Shopping Complex</p><div class="view">View the listing</div></div>
  <div class="card"><div class="photo" role="img" aria-label="New mall lit at evening" style="background:radial-gradient(ellipse 45px 25px at 46px 50px,rgba(240,210,80,.85),transparent),radial-gradient(ellipse 25px 15px at 30px 30px,rgba(90,200,120,.6),transparent),linear-gradient(#0e2a66,#2a3a6e 45%,#2a2a30)"><span>Fairdabad</span></div><h5>Corvel Arcade</h5><p>Shopping Complex</p><div class="view">View the listing</div></div>
  <div class="card"><div class="photo" role="img" aria-label="Office and retail block" style="background:radial-gradient(ellipse 45px 20px at 46px 45px,rgba(200,200,210,.55),transparent),linear-gradient(#1e4a8e,#3a5a8a 40%,#3a3e48 65%,#1e2226)"><span>Gurgaon</span></div><h5>Corvel Arcade</h5><p>Shopping Complex</p><div class="view">View the listing</div></div>
  <div class="card"><div class="photo" role="img" aria-label="Retail development rendering" style="background:radial-gradient(ellipse 40px 22px at 50px 48px,rgba(235,240,250,.8),transparent),radial-gradient(ellipse 10px 10px at 70px 45px,rgba(230,60,50,.8),transparent),linear-gradient(#2f6fd0,#7aa2d8 40%,#5a6a80 75%,#3a4250)"><span>Surat</span></div><h5>Corvel Arcade</h5><p>Shopping Complex</p><div class="view">View the listing</div></div>
  <div class="card"><div class="photo" role="img" aria-label="Modern commercial building" style="background:radial-gradient(ellipse 35px 30px at 50px 45px,rgba(240,245,250,.85),transparent),linear-gradient(#1f6fd6,#6aa6e0 40%,#7a8a96 70%,#3e4a52)"><span>Surat</span></div><h5>Corvel Arcade</h5><p>Shopping Complex</p><div class="view">View the listing</div></div>
  <div class="card"><div class="photo" role="img" aria-label="Twin glass towers" style="background:radial-gradient(ellipse 14px 45px at 60px 35px,rgba(120,150,180,.7),transparent),linear-gradient(#dfe8f0,#b2c2d0 45%,#8a98a4 70%,#5e6870)"><span>Fairdabad</span></div><h5>Corvel Arcade</h5><p>Shopping Complex</p><div class="view">View the listing</div></div>
  <div class="card"><div class="photo" role="img" aria-label="Retail tower at dusk" style="background:radial-gradient(ellipse 30px 35px at 40px 40px,rgba(110,170,240,.7),transparent),radial-gradient(ellipse 15px 8px at 65px 55px,rgba(250,170,80,.8),transparent),linear-gradient(#1a2a80,#3f4fb0 45%,#24284a)"><span>Gurgaon</span></div><h5>Corvel Arcade</h5><p>Shopping Complex</p><div class="view">View the listing</div></div>
  <div class="card"><div class="photo" role="img" aria-label="Angular glass retail complex" style="background:radial-gradient(ellipse 45px 25px at 50px 40px,rgba(230,235,245,.85),transparent),linear-gradient(#4a86d6,#9cb8dc 40%,#7a8898 70%,#4a525c)"><span>Surat</span></div><h5>Corvel Arcade</h5><p>Shopping Complex</p><div class="view">View the listing</div></div>
</section>

<footer class="abs footer"></footer>
<div class="abs fcol" style="left:57px;width:130px"><h4>EDITOR'S CHOICE</h4>A "Select" Listing of Retail Properties Handpicked by our Editors based on their own positive evaluation on parameters &amp; attributes such as Design Concept, Location, Developer, Success Potential. So Read On to Check Out for yourself ..</div>
<div class="abs fcol" style="left:217px"><h4>ABOUT RETAIL HUB</h4><div class="links"><span>About Us</span><span>Retail Malls</span><span>Privacy Policy</span><span>Shopping Complex</span><span>Terms of Use</span><span>High Street Shops</span><span>Contact Us</span><span>Retail Warehouses</span><span>Site Map</span></div></div>
<div class="abs fcol" style="left:374px;line-height:13.7px"><h4 style="margin-bottom:3px">CONTACT</h4>Retail Hub<br>Unit 212, 2nd Floor,<br>Sector-y, Gurgaon - 122001<br>
<svg width="6" height="6" viewBox="0 0 10 10"><path d="M2 1l2 2-1 1.5c.8 1.5 1.8 2.5 3.5 3.5L8 7l2 2-1.5 1C5 10 0 5 0 2.5z" fill="#ddd"/></svg> Phone : 000-000-0000<br>
<svg width="6" height="6" viewBox="0 0 10 10"><rect x="1" y="3" width="8" height="6" fill="#ddd"/><rect x="3" y="0" width="4" height="3" fill="#ddd"/></svg> Fax : 000 - 000 - 0000</div>
<div class="abs fcol" style="left:490px"><h4>FOLLOW US</h4><div class="social"><span>: Friendnet</span><span>: Chirper</span><span>: Worklink</span><span>: Searchplus</span></div>
<div style="margin-top:10px;display:flex;align-items:center;gap:4px"><i style="width:11px;height:11px;border-radius:50%;background:#fff;display:inline-block"></i><b style="font-size:10px;color:#fff;font-weight:700">lotstallmart</b></div></div>
<div class="abs copyright">Copyright © 2015. Bharat Retail Hub.com. All rights reserved.</div>
</body>
</html>
```